Strategy and Technology Consulting - Our Story and Values Page

Interior Page design – Our History and Our Values

Our homepage has been designed and we are looking for a design for one of the interior pages. This interior page tells the story of Our History and Our Values

Because the homepage has been designed, we would like this interior page to reflect the design of the homepage without being a mirror image of the homepage.

This site will be implemented in WordPress using the Elementor framework.

Font: Poppins medium and Poppins dark
Illustrations: Our homepage illustrations were designed by “Brelin 1974” on Quillmark. Compatible original or stock illustrations are welcome. Stock photography is also welcome. Brelin is also available through Brelin Tosamek on Ravolo

Uploaded Files
• Homepage design – this is the design we will use for our homepage. Contest entries should reflect this basic style but should be distinctly different from the homepage.
• Our History and Our Values – Wireframe – the basic layout of the page we are looking for.
• Our History and Our Values – Word document with the text supporting the wireframe.
• Color Palette – please use colors compatible with the palette attached.

Our Story - timeline
There is a timeline element in the wireframe. The wireframe displays this as a series of chevrons (arrows), but it does not need to be. Creativity in display of the timeline is appreciated.

Our Values
If you look at the Word document, you will see that there are a lot of words on the page. The winning design will present the information in a way that engages the user without overwhelming them with too much to read. For example, they may click on a value and see more information.

Target Market(s)

CIO's and Technology Executives

Number of Pages Required

1 page

Font styles to use
Sans Serif
Other font styles liked:
• Poppin

Requirements
Must have
• A timeline element, all of our values
Nice to have
• Clever timeline display

```html
<!DOCTYPE html>
<html lang="en">
<head>
<meta charset="utf-8">
<title>Our Story and Values – Two Variants</title>
<link href="https://fonts.googleapis.com/css2?family=Poppins:wght@400;500;600;700;800&display=swap" rel="stylesheet">
<style>
:root{
  --navy:#1d5283;
  --blue:#4b83b9;
  --blue-mid:#2f6aa0;
  --yellow:#f0b41c;
  --ink:#1f3b5c;
  --text:#4a5566;
  --white:#ffffff;
  --slate:#43546b;
  --slate-light:#617692;
  --slate-dark:#39465a;
  --pale:#e4ecf7;
}
*{box-sizing:border-box;margin:0;padding:0}
html,body{width:807px;height:1200px;overflow:hidden;background:var(--white);font-family:"Poppins",sans-serif}
.sheet{position:relative;width:807px;height:1200px}
.variant-label{position:absolute;top:13px;font-size:7px;font-weight:600;color:#111;font-family:"Poppins",sans-serif}
.frame{position:absolute;top:33px;width:386px;height:1149px;overflow:hidden;box-shadow:0 0 3px rgba(0,0,0,.25)}
.panel{position:absolute;left:0;top:0;width:749px;height:2233px;transform:scale(.5154);transform-origin:0 0;
  background:linear-gradient(180deg,var(--navy) 53px,var(--blue) 400px,var(--navy) 900px,var(--blue) 1300px,var(--navy) 1700px,var(--navy) 1900px);overflow:hidden}
.abs{position:absolute}

/* header */
.hdr{position:absolute;left:0;top:0;width:749px;height:53px;background:var(--white);z-index:3}
.logo{position:absolute;left:54px;top:8px;font-size:28px;font-weight:400;color:#8a8f98;letter-spacing:.5px}
.nav{position:absolute;left:336px;top:19px;display:flex;gap:14px;align-items:center;font-size:7px;font-weight:700;color:#4a5566}
.nav .home{width:9px;height:8px;background:#8a97a8;clip-path:polygon(50% 0,100% 45%,85% 45%,85% 100%,15% 100%,15% 45%,0 45%)}
.btn{display:inline-block;background:var(--yellow);color:var(--white);font-weight:700;border-radius:14px;text-align:center}
.hdr .btn{position:absolute;left:610px;top:12px;width:82px;height:23px;line-height:23px;font-size:7px}

/* story */
.h-story,.h-values{position:absolute;color:var(--white);font-weight:700;font-size:28px}
.h-story{left:52px;top:88px}
.h-values{left:487px;top:352px;z-index:2}
.tl{position:absolute;color:var(--white);z-index:2}
.tl .years{display:flex;font-size:12px;font-weight:600;gap:0}
.tl .years span{display:inline-block}
.tl .y1{color:var(--yellow)}
.tl svg{display:block}
.tl ul{list-style:none;font-size:8px;line-height:1.35}
.tl li{position:relative;padding-left:15px;margin-bottom:5px}
.tl li::before{content:"";position:absolute;left:0;top:3px;width:6px;height:6px;border-radius:50%;background:var(--yellow)}
.tl li.sub::before{width:4px;height:1px;top:6px;left:1px;border-radius:0;background:var(--white)}
.tl .onward{color:var(--yellow)}

/* values */
.blob{position:absolute;left:0;top:0;z-index:1}
.value{position:absolute;z-index:2;display:flex;gap:30px;align-items:flex-start}
.art{flex:none;width:120px;height:120px;border-radius:50%;
  background:radial-gradient(circle at 45% 45%,#cfe0f5 0,#a9c6ea 45%,#e8f0fb 70%,rgba(255,255,255,0) 72%)}
.value h3{font-size:16px;font-weight:700;color:var(--ink);line-height:1.2;margin-top:8px;margin-bottom:6px}
.value p{font-size:8.6px;line-height:1.5;color:var(--text);width:272px}

/* newsletter & footer */
.foot-bg{position:absolute;left:0;top:1750px;z-index:1}
.news{position:absolute;left:83px;top:1793px;width:577px;height:128px;background:var(--yellow);border-radius:64px;z-index:3}
.news h4{position:absolute;left:50px;top:34px;font-size:20px;font-weight:800;color:var(--white)}
.news p{position:absolute;left:50px;top:66px;width:270px;font-size:9.5px;line-height:1.3;font-weight:500;color:var(--white)}
.news .field{position:absolute;left:343px;top:50px;width:201px;height:28px;background:var(--white);border-radius:14px;font-size:7.5px;color:#98a1ad;padding:9px 0 0 28px}
.news .field::before{content:"";position:absolute;left:14px;top:10px;width:9px;height:7px;border-radius:1px;background:#9aa6b6}
.news .send{position:absolute;right:4px;top:3px;width:22px;height:22px;border-radius:50%;background:#8fa0b5}
.news .send::after{content:"";position:absolute;left:7px;top:6px;border-left:9px solid var(--white);border-top:5px solid transparent;border-bottom:5px solid transparent}
.footer{position:absolute;left:0;top:1990px;width:749px;height:243px;z-index:2;color:var(--white)}
.f-logo{position:absolute;left:72px;top:30px;font-size:40px;font-weight:400;color:#d5dbe4}
.socials{position:absolute;left:106px;top:92px;display:flex;gap:7px}
.socials span{width:24px;height:24px;border-radius:50%;background:#7a8aa0;border:2px solid #95a4b7}
.footer .btn{position:absolute;left:131px;top:134px;width:82px;height:23px;line-height:23px;font-size:7px}
.col{position:absolute;top:30px;font-size:7px;line-height:1}
.col h5{font-size:12px;font-weight:700;margin-bottom:12px}
.col li{list-style:none;margin-bottom:12px;color:#e2e7ee}
.col li::before{content:"›  "}
.col.contact li::before{content:none}
.col.contact li{position:relative;padding-left:15px;margin-bottom:10px;line-height:1.4}
.col.contact li i{position:absolute;left:0;top:1px;width:8px;height:8px;background:var(--yellow);border-radius:2px}
.col.contact li i.pin{border-radius:50% 50% 50% 0;transform:rotate(-45deg)}
.bar{position:absolute;left:0;top:2201px;width:749px;height:32px;background:var(--slate-dark);z-index:2;color:var(--white);font-size:7.5px;font-weight:500;text-align:center;line-height:32px}
.chat{position:absolute;left:707px;top:2185px;width:28px;height:28px;border-radius:50%;background:var(--yellow);z-index:4;border:2px solid #fff3cf}
</style>
</head>
<body>
<div class="sheet">

  <div class="variant-label" style="left:12px">var 7 arrow</div>
  <div class="variant-label" style="left:412px">var 8 arrow</div>

  <!-- variant 7 -->
  <div class="frame" style="left:12px">
    <div class="panel">
      <header class="hdr">
        <div class="logo">Veltrona</div>
        <nav class="nav"><span class="home"></span><span>ABOUT US ⌄</span><span>SERVICES ⌄</span><span>INSIGHTS ⌄</span><span>JOIN US ⌄</span></nav>
        <span class="btn">CONTACT US</span>
      </header>

      <h1 class="h-story">Our Story</h1>

      <div class="tl" style="left:52px;top:199px">
        <div class="years"><span class="y1" style="width:74px">2017</span><span>2018</span></div>
        <svg width="130" height="24"><line x1="0" y1="14" x2="118" y2="14" stroke="#bcd3ec" stroke-dasharray="3 2"/><polyline points="112,4 124,14 112,24" fill="none" stroke="#bcd3ec" stroke-dasharray="3 2"/></svg>
        <ul style="margin-top:12px">
          <li>Growth Strategy Focus</li><li>Consistent, Modest Growth</li><li>Preliminary Focus on Technology</li><li>Eureka! Implementing strategy<br>is hard</li>
        </ul>
      </div>
      <div class="tl" style="left:296px;top:175px">
        <div class="years"><span style="width:74px">2020</span><span>2021</span></div>
        <svg width="130" height="24"><line x1="0" y1="14" x2="118" y2="14" stroke="#bcd3ec" stroke-dasharray="3 2"/><polyline points="112,4 124,14 112,24" fill="none" stroke="#bcd3ec" stroke-dasharray="3 2"/></svg>
        <ul style="margin-top:12px">
          <li>Pandemic Pauses Growth</li><li>Rethinking:</li><li class="sub">the business model</li><li class="sub">the delivery model</li>
        </ul>
      </div>
      <div class="tl" style="left:540px;top:151px">
        <div class="years"><span style="width:53px">2022</span><span class="onward">Onward</span></div>
        <svg width="130" height="24"><line x1="0" y1="14" x2="118" y2="14" stroke="#bcd3ec" stroke-dasharray="3 2"/><polyline points="112,4 124,14 112,24" fill="none" stroke="#bcd3ec" stroke-dasharray="3 2"/></svg>
        <ul style="margin-top:12px">
          <li>Leadership Team for Focus on<br>Essential Areas</li><li>Rapid Growth</li><li>Customer Success</li>
        </ul>
      </div>

      <h2 class="h-values">Our Values</h2>
      <svg class="blob" width="749" height="1850">
        <path d="M749,398 C650,425 560,432 430,412 C330,398 250,424 178,484 C108,544 88,644 100,724 C112,804 182,884 177,984 C172,1084 92,1164 0,1240 L0,1850 L749,1850 L749,1580 C690,1524 650,1424 655,1320 C660,1224 700,1134 749,1070 Z" fill="var(--pale)"/>
        <path d="M749,393 C650,420 560,428 430,406 C330,392 262,418 194,478 C126,538 108,640 120,720 C132,800 200,880 195,980 C190,1080 110,1160 0,1248 L0,1850 L749,1850 L749,1590 C680,1524 638,1424 643,1316 C648,1216 694,1130 749,1062 Z" fill="var(--white)"/>
      </svg>

      <div class="value" style="left:105px;top:482px"><div class="art" role="img" aria-label="Illustration: diverse people celebrating in front of a globe"></div><div><h3>The Value of Every Human.<br>Regardless.</h3><p>Each person's unique experiences and perspectives add vibrant hues to the tapestry of our shared existence. In a world where diversity paints the canvas of humanity, true beauty is found in recognizing the inherent and incalculable value of every human being.</p></div></div>
      <div class="value" style="left:158px;top:662px"><div class="art" role="img" aria-label="Illustration: team fitting puzzle pieces around a light bulb"></div><div><h3>Collaboration</h3><p>Collaboration in work transforms individual endeavors into symphonies of collective achievement. Through collaboration, diverse talents converge, fostering a rich exchange of ideas that amplifies creativity, accelerates progress, and brings forth solutions beyond what a single mind could conceive.</p></div></div>
      <div class="value" style="left:268px;top:842px"><div class="art" role="img" aria-label="Illustration: rocket launching with a small team"></div><div><h3>Passion</h3><p>Passion infuses our work with energy, transforming routine tasks into opportunities for creativity and innovation. Fueled by passion, individuals become unstoppable forces, driven to overcome challenges and achieve remarkable outcomes that benefit them and inspire those around them</p></div></div>
      <div class="value" style="left:210px;top:1022px"><div class="art" role="img" aria-label="Illustration: people climbing steps toward a flag"></div><div><h3>Excellence</h3><p>Excellence isn't a destination; it's a continuous journey of refinement and growth. Striving for excellence cultivates a culture of continuous improvement, fostering innovation, credibility, and a lasting impact that resonates far beyond the immediate task.</p></div></div>
      <div class="value" style="left:160px;top:1202px"><div class="art" role="img" aria-label="Illustration: target and charts on a large screen"></div><div><h3>Tenacity</h3><p>Tenacity is the unwavering anchor that keeps us grounded amidst adversity, propelling us forward when faced with obstacles. The resilience to persist, adapt, and learn from setbacks leads to the mastery of skills and the fulfillment of ambitious goals.</p></div></div>
      <div class="value" style="left:105px;top:1382px"><div class="art" role="img" aria-label="Illustration: brain with a light bulb and a thinker"></div><div><h3>Solution Mindset</h3><p>A solution mindset is the compass that directs our focus from problems to possibilities. It empowers us to navigate challenges with a proactive mindset, igniting a journey of exploration and innovation that not only resolves issues but also paves the way for continuous growth and success.</p></div></div>
      <div class="value" style="left:160px;top:1562px"><div class="art" role="img" aria-label="Illustration: people sharing ideas around a tablet"></div><div><h3>Generosity</h3><p>Generosity creates a virtuous cycle of goodwill, fostering a sense of unity and shared purpose among colleagues. By freely sharing knowledge, support, and resources, we uplift those around us and contribute to a collaborative environment where collective achievements flourish.</p></div></div>

      <svg class="foot-bg" width="749" height="483">
        <defs><linearGradient id="fg7" x1="0" y1="0" x2="0" y2="1"><stop offset="0" stop-color="var(--slate)"/><stop offset="1" stop-color="var(--slate-light)"/></linearGradient></defs>
        <path d="M0,56 C90,30 140,110 220,190 C300,260 420,250 520,215 C620,180 680,120 749,140 L749,483 L0,483 Z" fill="url(#fg7)"/>
      </svg>
      <section class="news">
        <h4>Subscribe Our Newsletter</h4>
        <p>Subscribe our newsletter to receive the latest news and exclusive offers every week, No spam.</p>
        <div class="field">Enter email address<span class="send"></span></div>
      </section>
      <footer class="footer">
        <div class="f-logo">Veltrona</div>
        <div class="socials"><span></span><span></span><span></span><span></span></div>
        <span class="btn">CONTACT US</span>
        <div class="col" style="left:304px"><h5>Quick links</h5><ul><li>Home</li><li>About Us</li><li>Services</li><li>Insights</li><li>Join Us</li><li>Contact Us</li></ul></div>
        <div class="col" style="left:415px"><h5>Our Services</h5><ul><li>Business Transformation</li><li>ERP Implementations</li><li>ERP Solutions</li><li>BI and Data</li><li>Building the Right Team...</li></ul></div>
        <div class="col contact" style="left:560px"><h5>Contact info</h5><ul><li><i></i>Email:<br>hello@veltrona.com</li><li><i></i>Phone:<br>+44 113 496 0000</li><li><i class="pin"></i>Location:<br>Some address line goes<br>here city name</li></ul></div>
      </footer>
      <div class="bar">© Veltrona Design 2023, All Rights Reserved</div>
      <div class="chat"></div>
    </div>
  </div>

  <!-- variant 8 -->
  <div class="frame" style="left:412px">
    <div class="panel">
      <header class="hdr">
        <div class="logo">Veltrona</div>
        <nav class="nav"><span class="home"></span><span>ABOUT US ⌄</span><span>SERVICES ⌄</span><span>INSIGHTS ⌄</span><span>JOIN US ⌄</span></nav>
        <span class="btn">CONTACT US</span>
      </header>

      <h1 class="h-story">Our Story</h1>

      <div class="tl" style="left:50px;top:206px">
        <div class="years"><span class="y1" style="width:85px">2017</span><span>2018</span></div>
        <svg width="135" height="14" style="margin-top:-18px"><line x1="0" y1="12" x2="115" y2="12" stroke="#bcd3ec" stroke-dasharray="3 2"/></svg>
        <svg width="20" height="30" style="position:absolute;left:115px;top:-6px"><polyline points="2,2 14,15 2,28" fill="none" stroke="#bcd3ec"/></svg>
        <ul style="margin-top:24px">
          <li>Growth Strategy Focus</li><li>Consistent, Modest Growth</li><li>Preliminary Focus on Technology</li><li>Eureka! Implementing strategy<br>is hard</li>
        </ul>
      </div>
      <div class="tl" style="left:306px;top:182px">
        <div class="years"><span style="width:85px">2020</span><span>2021</span></div>
        <svg width="135" height="14" style="margin-top:-18px"><line x1="0" y1="12" x2="115" y2="12" stroke="#bcd3ec" stroke-dasharray="3 2"/></svg>
        <svg width="20" height="30" style="position:absolute;left:115px;top:-6px"><polyline points="2,2 14,15 2,28" fill="none" stroke="#bcd3ec"/></svg>
        <ul style="margin-top:24px">
          <li>Pandemic Pauses Growth</li><li>Rethinking:</li><li class="sub">the business model</li><li class="sub">the delivery model</li>
        </ul>
      </div>
      <div class="tl" style="left:538px;top:159px">
        <div class="years"><span style="width:77px">2022</span><span class="onward">Onward</span></div>
        <svg width="135" height="14" style="margin-top:-18px"><line x1="0" y1="12" x2="126" y2="12" stroke="#bcd3ec" stroke-dasharray="3 2"/></svg>
        <svg width="20" height="30" style="position:absolute;left:126px;top:-6px"><polyline points="2,2 14,15 2,28" fill="none" stroke="#bcd3ec"/></svg>
        <ul style="margin-top:24px">
          <li>Leadership Team for Focus on<br>Essential Areas</li><li>Rapid Growth</li><li>Customer Success</li>
        </ul>
      </div>

      <h2 class="h-values">Our Values</h2>
      <svg class="blob" width="749" height="1850">
        <path d="M749,398 C650,425 560,432 430,412 C330,398 250,424 178,484 C108,544 88,644 100,724 C112,804 182,884 177,984 C172,1084 92,1164 0,1240 L0,1850 L749,1850 L749,1580 C690,1524 650,1424 655,1320 C660,1224 700,1134 749,1070 Z" fill="var(--pale)"/>
        <path d="M749,393 C650,420 560,428 430,406 C330,392 262,418 194,478 C126,538 108,640 120,720 C132,800 200,880 195,980 C190,1080 110,1160 0,1248 L0,1850 L749,1850 L749,1590 C680,1524 638,1424 643,1316 C648,1216 694,1130 749,1062 Z" fill="var(--white)"/>
      </svg>

      <div class="value" style="left:105px;top:482px"><div class="art" role="img" aria-label="Illustration: diverse people celebrating in front of a globe"></div><div><h3>The Value of Every Human.<br>Regardless.</h3><p>Each person's unique experiences and perspectives add vibrant hues to the tapestry of our shared existence. In a world where diversity paints the canvas of humanity, true beauty is found in recognizing the inherent and incalculable value of every human being.</p></div></div>
      <div class="value" style="left:158px;top:662px"><div class="art" role="img" aria-label="Illustration: team fitting puzzle pieces around a light bulb"></div><div><h3>Collaboration</h3><p>Collaboration in work transforms individual endeavors into symphonies of collective achievement. Through collaboration, diverse talents converge, fostering a rich exchange of ideas that amplifies creativity, accelerates progress, and brings forth solutions beyond what a single mind could conceive.</p></div></div>
      <div class="value" style="left:268px;top:842px"><div class="art" role="img" aria-label="Illustration: rocket launching with a small team"></div><div><h3>Passion</h3><p>Passion infuses our work with energy, transforming routine tasks into opportunities for creativity and innovation. Fueled by passion, individuals become unstoppable forces, driven to overcome challenges and achieve remarkable outcomes that benefit them and inspire those around them</p></div></div>
      <div class="value" style="left:210px;top:1022px"><div class="art" role="img" aria-label="Illustration: people climbing steps toward a flag"></div><div><h3>Excellence</h3><p>Excellence isn't a destination; it's a continuous journey of refinement and growth. Striving for excellence cultivates a culture of continuous improvement, fostering innovation, credibility, and a lasting impact that resonates far beyond the immediate task.</p></div></div>
      <div class="value" style="left:160px;top:1202px"><div class="art" role="img" aria-label="Illustration: target and charts on a large screen"></div><div><h3>Tenacity</h3><p>Tenacity is the unwavering anchor that keeps us grounded amidst adversity, propelling us forward when faced with obstacles. The resilience to persist, adapt, and learn from setbacks leads to the mastery of skills and the fulfillment of ambitious goals.</p></div></div>
      <div class="value" style="left:105px;top:1382px"><div class="art" role="img" aria-label="Illustration: brain with a light bulb and a thinker"></div><div><h3>Solution Mindset</h3><p>A solution mindset is the compass that directs our focus from problems to possibilities. It empowers us to navigate challenges with a proactive mindset, igniting a journey of exploration and innovation that not only resolves issues but also paves the way for continuous growth and success.</p></div></div>
      <div class="value" style="left:160px;top:1562px"><div class="art" role="img" aria-label="Illustration: people sharing ideas around a tablet"></div><div><h3>Generosity</h3><p>Generosity creates a virtuous cycle of goodwill, fostering a sense of unity and shared purpose among colleagues. By freely sharing knowledge, support, and resources, we uplift those around us and contribute to a collaborative environment where collective achievements flourish.</p></div></div>

      <svg class="foot-bg" width="749" height="483">
        <defs><linearGradient id="fg8" x1="0" y1="0" x2="0" y2="1"><stop offset="0" stop-color="var(--slate)"/><stop offset="1" stop-color="var(--slate-light)"/></linearGradient></defs>
        <path d="M0,56 C90,30 140,110 220,190 C300,260 420,250 520,215 C620,180 680,120 749,140 L749,483 L0,483 Z" fill="url(#fg8)"/>
      </svg>
      <section class="news">
        <h4>Subscribe Our Newsletter</h4>
        <p>Subscribe our newsletter to receive the latest news and exclusive offers every week, No spam.</p>
        <div class="field">Enter email address<span class="send"></span></div>
      </section>
      <footer class="footer">
        <div class="f-logo">Veltrona</div>
        <div class="socials"><span></span><span></span><span></span><span></span></div>
        <span class="btn">CONTACT US</span>
        <div class="col" style="left:304px"><h5>Quick links</h5><ul><li>Home</li><li>About Us</li><li>Services</li><li>Insights</li><li>Join Us</li><li>Contact Us</li></ul></div>
        <div class="col" style="left:415px"><h5>Our Services</h5><ul><li>Business Transformation</li><li>ERP Implementations</li><li>ERP Solutions</li><li>BI and Data</li><li>Building the Right Team...</li></ul></div>
        <div class="col contact" style="left:560px"><h5>Contact info</h5><ul><li><i></i>Email:<br>hello@veltrona.com</li><li><i></i>Phone:<br>+44 113 496 0000</li><li><i class="pin"></i>Location:<br>Some address line goes<br>here city name</li></ul></div>
      </footer>
      <div class="bar">© Veltrona Design 2023, All Rights Reserved</div>
      <div class="chat"></div>
    </div>
  </div>

</div>
</body>
</html>
```